New letter head for Air Conditioning business

We need a new professional letter head design to suit our new re-branded air conditioning business. Our new logo is attached

```html
<!DOCTYPE html>
<html lang="en">
<head>
<meta charset="utf-8">
<title>Norvale Letterhead</title>
<link rel="stylesheet" href="https://fonts.googleapis.com/css2?family=Open+Sans:wght@400;600;700&display=swap">
<style>
  :root {
    --backdrop: #ececec;
    --paper: #ffffff;
    --ink: #2b2b2b;
    --ink-soft: #6f6f6f;
    --brand-green: #5fbf84;
    --brand-red: #ee6451;
    --brand-dark: #33363b;
    --signature-tint: #eef0f2;
  }
  * { box-sizing: border-box; margin: 0; padding: 0; }
  html, body {
    width: 1200px; height: 794px; overflow: hidden;
    background: var(--backdrop);
    font-family: "Open Sans", Arial, sans-serif;
    color: var(--ink);
  }
  .letterhead {
    position: absolute; left: 338px; top: 27px;
    width: 524px; height: 740px;
    background: var(--paper);
    box-shadow: 0 6px 18px rgba(0,0,0,0.12);
    overflow: hidden;
  }
  .brand {
    position: absolute; left: 40px; top: 46px;
    display: flex; align-items: center; gap: 8px;
  }
  .brand-dot {
    width: 22px; height: 22px; border-radius: 50%;
    background: var(--brand-green);
  }
  .brand-text { display: flex; flex-direction: column; }
  .brand-name {
    font-size: 22px; font-weight: 700; letter-spacing: 3px;
    color: var(--brand-dark); line-height: 1;
  }
  .brand-tagline {
    font-size: 5px; letter-spacing: 1px; text-transform: uppercase;
    color: var(--ink-soft); margin-top: 3px;
  }
  .contact-list {
    position: absolute; right: 40px; top: 40px;
    list-style: none; font-size: 7px; color: var(--ink-soft);
  }
  .contact-list li { display: flex; align-items: center; gap: 5px; line-height: 11px; }
  .contact-icon {
    width: 8px; height: 8px; border-radius: 50%;
    display: inline-flex; align-items: center; justify-content: center;
  }
  .contact-icon.green { background: var(--brand-green); }
  .contact-icon.red { background: var(--brand-red); }
  .letter-body {
    position: absolute; left: 40px; top: 150px; width: 440px;
    font-size: 7.2px; line-height: 11px; color: var(--ink-soft);
  }
  .letter-date, .recipient { color: var(--ink); font-size: 8px; line-height: 11px; }
  .recipient { margin-top: 12px; font-style: normal; }
  .salutation { margin: 12px 0 10px; font-weight: 700; color: var(--ink); font-size: 8.5px; }
  .letter-body p { margin-bottom: 11px; }
  .sign-off {
    position: absolute; left: 330px; top: 420px; width: 150px;
    font-size: 8px; color: var(--ink); line-height: 11px;
  }
  .signature {
    width: 110px; height: 30px; margin: 6px 0 6px;
    background: var(--signature-tint); border-radius: 4px;
  }
  .footer-address {
    position: absolute; left: 330px; top: 510px;
    display: flex; gap: 5px; font-size: 8px; line-height: 10px;
    color: var(--ink); font-style: normal;
  }
  .footer-company { color: var(--brand-red); font-weight: 700; }
  .footer-accent {
    position: absolute; left: 0; bottom: 0;
    width: 524px; height: 110px;
    background: linear-gradient(100deg, var(--brand-green) 0%, var(--brand-green) 45%, var(--brand-red) 100%);
  }
</style>
</head>
<body>
  <main class="letterhead">
    <header class="brand">
      <span class="brand-dot"></span>
      <div class="brand-text">
        <span class="brand-name">NORVALE</span>
        <span class="brand-tagline">Air Conditioning &amp; Refrigeration</span>
      </div>
    </header>

    <ul class="contact-list">
      <li><span class="contact-icon green"><svg width="5" height="5" viewBox="0 0 10 10"><path d="M2 1l2 2-1 1.5a6 6 0 0 0 2.5 2.5L7 6l2 2-1.5 1.5C4 9 1 6 .5 2.5z" fill="#fff"/></svg></span>(555) 010-2481</li>
      <li><span class="contact-icon red"><svg width="5" height="5" viewBox="0 0 10 10"><path d="M2 1l2 2-1 1.5a6 6 0 0 0 2.5 2.5L7 6l2 2-1.5 1.5C4 9 1 6 .5 2.5z" fill="#fff"/></svg></span>(555) 010-2482</li>
      <li><span class="contact-icon green"><svg width="5" height="5" viewBox="0 0 10 10"><rect x="1" y="2" width="8" height="6" fill="none" stroke="#fff" stroke-width="1.4"/><path d="M1 2l4 3 4-3" fill="none" stroke="#fff" stroke-width="1.2"/></svg></span>info@norvaleair.com</li>
      <li><span class="contact-icon red"><svg width="5" height="5" viewBox="0 0 10 10"><circle cx="5" cy="5" r="4" fill="none" stroke="#fff" stroke-width="1.4"/><path d="M1 5h8M5 1v8" stroke="#fff" stroke-width="1"/></svg></span>www.norvaleair.com</li>
    </ul>

    <section class="letter-body">
      <div class="letter-date">January 03, 2017</div>
      <address class="recipient">
        Mr. John Doe<br>President<br>AA Corporation<br>111 Street Name, Suite#<br>City, State, 12345
      </address>
      <div class="salutation">Dear Mr. John,</div>
      <p>Lorem Ipsum is simply dummy text of the printing and typesetting industry. Lorem Ipsum has been the industry's standard dummy text ever since the 1500s, when an unknown printer took a galley of type and scrambled it to make a type specimen book. It has survived not only five centuries, but also the leap into electronic typesetting, remaining essentially unchanged.</p>
      <p>The standard chunk of Lorem Ipsum used since the 1500s is reproduced below for those interested. Sections 1.10.32 and 1.10.33 from "de Finibus Bonorum et Malorum" by Cicero are also reproduced in their exact original form, accompanied by English versions from the 1914 translation by H. Rackham.</p>
      <p>Lorem Ipsum is simply dummy text of the printing and typesetting industry. Lorem Ipsum has been the industry's standard dummy text ever since the 1500s, when an unknown printer took a galley of type and scrambled it to make a type specimen book. It has survived not only five centuries, but also the leap into electronic typesetting, remaining essentially unchanged. It was popularised in the</p>
    </section>

    <section class="sign-off">
      <div>Sincerely Your,</div>
      <div class="signature" role="img" aria-label="Handwritten signature"></div>
      <div>Name Last Name</div>
      <div>Company Name</div>
    </section>

    <address class="footer-address">
      <svg width="8" height="11" viewBox="0 0 8 11"><path d="M4 0a4 4 0 0 1 4 4c0 3-4 7-4 7S0 7 0 4a4 4 0 0 1 4-4z" fill="var(--brand-red)"/><circle cx="4" cy="4" r="1.5" fill="#fff"/></svg>
      <div><span class="footer-company">NORVALE</span><br>Suite 102 Street name, State,<br>Zip 2034, Country</div>
    </address>

    <div class="footer-accent" role="img" aria-label="Decorative footer graphic in brand green and red"></div>
  </main>
</body>
</html>
```